Harbourline Electrical Solutions

On one side. LOGO (underneath:) Commercial Industrial Residential

- NAME & CONTACT DETAILS

Marcus T. Hollings
Project Manager

(Cell icon) (441) 555-0187
(Email icon) hlelectricalsolutions@mailvento.com
(Facebook & Instagram icons )@hlelectricalsolutions

Other side: LOGO - underneath ELECTRICAL CONSTRUCTION & MAINTENANCE . LED LIGHTING & AUTOMATION . LIFE SAFETY SYSTEMS (FIRE ALARM / SECURITY) . DATA & COMMUNICATION

```html
<!DOCTYPE html>
<html lang="en">
<head>
<meta charset="utf-8">
<title>Harbourline Electrical Solutions – Business Cards</title>
<link rel="stylesheet" href="https://fonts.googleapis.com/css2?family=Montserrat:wght@600&family=Roboto:wght@400&family=Exo+2:ital,wght@1,700&display=swap">
<style>
  :root {
    --brand: #0e5a78;
    --ink: #3b3f43;
    --card: #ffffff;
    --backdrop: #3a3a3c;
    --band-text: #ffffff;
  }
  * { box-sizing: border-box; margin: 0; padding: 0; }
  html, body { width: 799px; height: 1200px; overflow: hidden; }
  body {
    background: var(--backdrop);
    font-family: "Roboto", Arial, sans-serif;
    position: relative;
  }
  .card {
    position: absolute;
    left: 50px;
    width: 700px;
    height: 400px;
    background: var(--card);
    box-shadow: 0 10px 30px rgba(0,0,0,.45);
    overflow: hidden;
  }
  .card--front { top: 120px; }
  .card--back  { top: 680px; }

  .brand-block { position: absolute; left: 60px; top: 46px; }
  .brand-name {
    display: flex; align-items: center; gap: 14px;
    font-family: "Montserrat", Arial, sans-serif;
    font-weight: 600;
    font-size: 34px;
    letter-spacing: 1px;
    color: var(--brand);
    text-transform: uppercase;
    line-height: 1.05;
  }
  .brand-mark { width: 58px; height: 58px; background: var(--brand); flex: none; }
  .brand-sectors {
    margin-top: 12px;
    font-family: "Montserrat", Arial, sans-serif;
    font-weight: 600;
    font-size: 15px;
    letter-spacing: 3px;
    color: var(--brand);
    text-transform: uppercase;
  }
  .brand-sectors .divider { color: var(--ink); margin: 0 10px; }

  .service-band {
    position: absolute; left: 0; top: 180px;
    width: 100%; height: 110px;
    background: var(--brand);
    color: var(--band-text);
    padding: 24px 60px;
    font-size: 19px;
    line-height: 30px;
  }
  .social-handle {
    position: absolute;
    display: flex; align-items: center; gap: 10px;
    font-size: 19px; color: var(--ink);
  }
  .social-handle .dot { width: 14px; height: 14px; border-radius: 50%; background: var(--brand); }
  .card--front .social-handle { left: 60px; top: 318px; }

  .person { position: absolute; left: 60px; top: 190px; }
  .person-name {
    font-family: "Exo 2", Arial, sans-serif;
    font-style: italic; font-weight: 700;
    font-size: 28px; color: var(--brand);
  }
  .person-role { font-size: 18px; color: var(--ink); margin-top: 2px; }
  .contact-list { list-style: none; margin-top: 14px; }
  .contact-list li {
    display: flex; align-items: center; gap: 12px;
    font-size: 18px; color: var(--ink); line-height: 30px;
  }
  .contact-list svg { width: 18px; height: 18px; fill: var(--brand); flex: none; }
  .rule {
    position: absolute; left: 300px; right: 60px; top: 262px;
    height: 2px; background: var(--brand);
  }
  .card--back .social-handle { right: 60px; top: 300px; }
</style>
</head>
<body>

<section class="card card--front" aria-label="Card front: services">
  <div class="brand-block">
    <div class="brand-name"><span class="brand-mark"></span><span>Harbourline<br>Electrical Solutions</span></div>
  </div>
  <div class="service-band">
    <p>Electrical Construction &amp; Maintenance &nbsp;|&nbsp; Led Lighting &amp; Automation</p>
    <p>Life Safety Systems (Fire Alarm/Security) &nbsp;|&nbsp; Data &amp; Communication</p>
  </div>
  <div class="social-handle"><span class="dot"></span>@hlelectricalsolutions</div>
  <div class="brand-sectors" style="position:absolute;left:60px;top:130px;">
    Commercial<span class="divider">|</span>Industrial<span class="divider">|</span>Residential
  </div>
</section>

<section class="card card--back" aria-label="Card back: contact details">
  <div class="brand-block">
    <div class="brand-name"><span class="brand-mark"></span><span>Harbourline<br>Electrical Solutions</span></div>
    <div class="brand-sectors">Commercial<span class="divider">|</span>Industrial<span class="divider">|</span>Residential</div>
  </div>
  <div class="person">
    <p class="person-name">Marcus T. Hollings</p>
    <p class="person-role">Project Manager</p>
    <ul class="contact-list">
      <li>
        <svg viewBox="0 0 24 24" aria-hidden="true"><path d="M6.6 10.8a15.1 15.1 0 0 0 6.6 6.6l2.2-2.2c.3-.3.7-.4 1-.2 1.1.4 2.3.6 3.6.6.6 0 1 .4 1 1V20c0 .6-.4 1-1 1A17 17 0 0 1 3 4c0-.6.4-1 1-1h3.5c.6 0 1 .4 1 1 0 1.3.2 2.5.6 3.6.1.3 0 .7-.2 1z"/></svg>
        (441) 555-0187
      </li>
      <li>
        <svg viewBox="0 0 24 24" aria-hidden="true"><path d="M2 5h20v14H2zm2 2v.5l8 5 8-5V7l-8 5z"/></svg>
        hlelectricalsolutions@mailvento.com
      </li>
    </ul>
  </div>
  <div class="rule"></div>
  <div class="social-handle"><span class="dot"></span>@hlelectricalsolutions</div>
</section>

</body>
</html>
```